RTavenor Business Cards & Letterhead

I have a logo but need a design for some new business cards. We are a Design-Build Firm that specializes in the design and construction of commercial projects.
the cards need to be professional. no cartoon stuff.
i would like to have the cards in AI format so I can update the card as needed. Logo is provided.
Our Address is: 4187 Marlowe Ct. Larkfield, Maine 27614

```html
<!DOCTYPE html>
<html lang="en">
<head>
<meta charset="UTF-8">
<title>RTavenor Business Cards</title>
<link href="https://fonts.googleapis.com/css2?family=Lato:wght@400;700;900&display=swap" rel="stylesheet">
<style>
  :root {
    --stage: #2b2b2b;
    --card-dark: #4a4a4a;
    --silver: #bdbdbd;
    --ink: #3b3b3b;
    --blue-deep: #003e6e;
    --blue: #0a6db3;
    --blue-bright: #1a86c8;
    --ice: #e3eff8;
    --ice-strong: #cfe2f0;
    --white: #ffffff;
  }
  * { margin: 0; padding: 0; box-sizing: border-box; }
  html, body {
    width: 1200px; height: 875px; overflow: hidden;
    background: var(--stage);
    font-family: 'Lato', sans-serif;
  }
  .sheet {
    width: 1200px; height: 875px;
    display: flex; align-items: center; justify-content: center; gap: 40px;
  }
  .card {
    width: 540px; height: 309px; border-radius: 22px;
    position: relative; overflow: hidden;
    box-shadow: 0 18px 40px rgba(0,0,0,.45);
  }
  /* Front */
  .card--front {
    background: var(--card-dark);
    display: flex; align-items: center; justify-content: center;
  }
  .brand { display: flex; align-items: center; gap: 12px; }
  .brand__mark { width: 26px; height: 26px; flex: none; }
  .brand__name {
    font-weight: 900; letter-spacing: 1px; text-transform: uppercase;
    line-height: 1; white-space: nowrap;
  }
  .brand__reg { font-size: 13px; font-weight: 400; vertical-align: top; margin-left: 2px; }
  .card--front .brand__mark { background: var(--silver); }
  .card--front .brand__name { font-size: 56px; color: var(--silver); }
  /* Back */
  .card--back {
    background: linear-gradient(180deg, var(--blue-bright) 0%, var(--blue) 45%, var(--blue-deep) 100%);
  }
  .back__panel {
    position: absolute; left: 0; top: 40px; bottom: 0; width: 296px;
    background: linear-gradient(135deg, var(--white) 0%, var(--ice) 55%, var(--ice-strong) 100%);
    border-radius: 28px 120px 0 0;
  }
  .back__panel .brand { position: absolute; left: 32px; top: 128px; gap: 10px; }
  .card--back .brand__mark { width: 18px; height: 18px; background: var(--blue); }
  .card--back .brand__name { font-size: 32px; color: var(--ink); }
  .back__details {
    position: absolute; right: 26px; top: 44px;
    color: var(--white); text-align: right;
  }
  .person__name { font-size: 24px; font-weight: 900; text-transform: uppercase; letter-spacing: .3px; line-height: 1.15; white-space: nowrap; }
  .person__role { font-size: 14px; margin-bottom: 14px; }
  .contact { list-style: none; font-size: 13px; line-height: 21px; }
  .contact li { display: flex; justify-content: flex-end; align-items: center; gap: 8px; white-space: nowrap; }
  .contact svg { width: 12px; height: 12px; fill: var(--white); flex: none; }
  .contact .spacer { width: 12px; flex: none; }
</style>
</head>
<body>
<main class="sheet">
  <section class="card card--front" aria-label="Card front">
    <div class="brand">
      <span class="brand__mark"></span>
      <span class="brand__name">RTavenor<span class="brand__reg">®</span></span>
    </div>
  </section>

  <section class="card card--back" aria-label="Card back">
    <div class="back__panel">
      <div class="brand">
        <span class="brand__mark"></span>
        <span class="brand__name">RTavenor<span class="brand__reg">®</span></span>
      </div>
    </div>
    <div class="back__details">
      <h1 class="person__name">Daniel Hartwell</h1>
      <p class="person__role">Founder &amp; CEO</p>
      <ul class="contact">
        <li>(919) 555-0142
          <svg viewBox="0 0 24 24"><path d="M6.6 10.8a15 15 0 0 0 6.6 6.6l2.2-2.2c.3-.3.7-.4 1-.2 1.1.4 2.3.6 3.6.6.6 0 1 .4 1 1V20c0 .6-.4 1-1 1A17 17 0 0 1 3 4c0-.6.4-1 1-1h3.5c.6 0 1 .4 1 1 0 1.3.2 2.5.6 3.6.1.3 0 .7-.2 1z"/></svg></li>
        <li>(919) 555-0187
          <svg viewBox="0 0 24 24"><path d="M7 1h10a2 2 0 0 1 2 2v18a2 2 0 0 1-2 2H7a2 2 0 0 1-2-2V3a2 2 0 0 1 2-2zm0 3v14h10V4zm5 15.5a1 1 0 1 0 0 2 1 1 0 0 0 0-2z"/></svg></li>
        <li>(919) 555-0163
          <svg viewBox="0 0 24 24"><path d="M6 2h12v5H6zM4 8h16a2 2 0 0 1 2 2v7h-4v5H6v-5H2v-7a2 2 0 0 1 2-2zm4 8v4h8v-4z"/></svg></li>
        <li>office@rtavenor-build.com
          <svg viewBox="0 0 24 24"><path d="M2 5h20v14H2zm2 2v.4l8 5 8-5V7z"/></svg></li>
        <li>www.rtavenor-build.com
          <svg viewBox="0 0 24 24"><path d="M12 2a10 10 0 1 0 0 20 10 10 0 0 0 0-20zm0 2c1 1.3 1.8 3.1 2.1 5H9.9C10.2 7.1 11 5.3 12 4zM4.3 11h3.5a15 15 0 0 0 .3 4H5a8 8 0 0 1-.7-4zm11.9 0h3.5a8 8 0 0 1-.7 4h-3.1a15 15 0 0 0 .3-4zm-6.4 0h4.4a13 13 0 0 1-.3 4h-3.8a13 13 0 0 1-.3-4z"/></svg></li>
        <li>4187 Marlowe Ct. Larkfield
          <svg viewBox="0 0 24 24"><path d="M12 2a7 7 0 0 0-7 7c0 5 7 13 7 13s7-8 7-13a7 7 0 0 0-7-7zm0 9.5a2.5 2.5 0 1 1 0-5 2.5 2.5 0 0 1 0 5z"/></svg></li>
        <li>Maine 27614<span class="spacer"></span></li>
      </ul>
    </div>
  </section>
</main>
</body>
</html>
```